The Lantern Guild Pitchdeck Template

The Lantern Guild would like a branded pitch deck template design for members to use when presenting their projects and proposals. The deck should include 10-15 different slide designs, each with the same branded theme, but with a variety of icon graphics and other design features that will empower members to easily create a beautiful pitch deck just by adding written content.

Please visit lanternguildhq.org to get a sense for our branding - purple, space, galaxy, white font and the planetary logo are some commonalities.

Here are 2 google drive links with some additional designs

https://files.boxmeadow.net/share/f/8QzrTa2Lk5VbNw7cHyP0dJe3sUmXg4RiF

https://files.boxmeadow.net/share/f/3Kd9-Rm6Tq2-yLvBn051fopwxhcT_zj7

```html
<!DOCTYPE html>
<html lang="en">
<head>
<meta charset="utf-8">
<title>The Lantern Guild – Pitch Deck Template</title>
<link href="https://fonts.googleapis.com/css2?family=Montserrat:wght@300;400;500;600;700&display=swap" rel="stylesheet">
<style>
:root{
  --page:#ffffff;
  --bg-deep:#1c0a30;
  --bg:#261040;
  --panel:#34165a;
  --violet:#7b3fc4;
  --lilac:#b48af0;
  --pale:#efe3ff;
  --text:#ffffff;
  --muted:#d9cbeb;
  --line:#7f52c0;
}
*{box-sizing:border-box;margin:0;padding:0}
html,body{width:847px;height:1200px;overflow:hidden;background:var(--page)}
body{position:relative;font-family:"Montserrat",sans-serif;color:var(--text)}
.slide{position:absolute;width:380px;height:214px;overflow:hidden;
  background:radial-gradient(circle at 70% 30%,var(--bg) 0%,var(--bg-deep) 80%)}
.c1{left:28px}.c2{left:418px}
.r1{top:22px}.r2{top:245px}.r3{top:469px}.r4{top:692px}.r5{top:916px}
.abs{position:absolute}
.brand{position:absolute;left:14px;top:12px;display:flex;align-items:center;gap:4px;
  font-weight:600;font-size:8.5px;letter-spacing:1.6px;white-space:nowrap}
.brand i{width:6px;height:6px;border-radius:50%;background:var(--lilac);display:block}
.title{position:absolute;font-weight:300;font-size:12px;letter-spacing:.3px;white-space:nowrap}
.title b{font-weight:700}
.center{left:0;right:0;text-align:center}
.rule{position:absolute;height:1px;background:var(--line)}
.body{position:absolute;font-size:4.4px;line-height:7.4px;color:var(--muted);text-align:justify}
.body p+p{margin-top:4px}
.photo{position:absolute;overflow:hidden}
.orbit{position:absolute;border-radius:50%;border:1px solid rgba(180,138,240,.18)}
.dot{position:absolute;border-radius:50%;background:var(--violet)}
.node{position:absolute;border-radius:50%;display:flex;flex-direction:column;align-items:center;justify-content:center;
  background:var(--bg-deep);box-shadow:0 0 0 5px rgba(123,63,196,.35);font-size:4.2px;font-weight:600;text-align:center}
.node svg{width:13px;height:13px;margin-bottom:3px}
.tier{position:absolute;display:flex;align-items:center;gap:7px;font-size:5.6px;font-weight:600;white-space:nowrap}
.tier span.ic{width:28px;height:28px;border-radius:50%;background:var(--pale);display:flex;align-items:center;justify-content:center}
.tier svg{width:13px;height:13px}
.vision{position:absolute;width:88px;height:88px;border-radius:50%;background:var(--panel);text-align:center;padding-top:34px}
.vision h4{font-size:5.3px;font-weight:600;margin-bottom:5px}
.vision p{font-size:3.9px;line-height:7px;color:var(--muted);padding:0 8px}
.vision .ic{position:absolute;left:26px;top:-20px;width:36px;height:36px;border-radius:50%;background:var(--pale);
  box-shadow:0 0 0 3px var(--violet);display:flex;align-items:center;justify-content:center}
.vision svg{width:20px;height:20px}
.list{position:absolute;list-style:none;font-size:4.5px;line-height:7.5px}
.list li::before{content:"";display:inline-block;border-left:2px solid #fff;border-top:1.5px solid transparent;border-bottom:1.5px solid transparent;margin-right:3px;vertical-align:0}
.step{position:absolute;width:80px;height:80px;border-radius:50%;border:6px solid var(--lilac);background:var(--bg-deep);
  display:flex;flex-direction:column;align-items:center;justify-content:center;font-size:4.8px;font-weight:600;text-align:center;line-height:6.5px}
.step svg{width:22px;height:22px;margin-bottom:5px}
.partner{position:absolute;width:90px;text-align:center}
.partner .badge{width:46px;height:46px;border-radius:50%;margin:0 auto 6px;border:1px solid var(--lilac);box-shadow:0 0 0 3px var(--bg-deep),0 0 0 4px rgba(180,138,240,.4)}
.partner h5{font-size:4.3px;font-weight:600}
.partner p{font-size:3.5px;color:var(--muted);line-height:5.2px;margin-top:2px}
.contact{position:absolute;display:flex;gap:6px;font-size:5.3px;line-height:8px}
.contact .ic{width:16px;height:16px;border-radius:50%;background:var(--pale);display:flex;align-items:center;justify-content:center;flex:none}
.contact svg{width:9px;height:9px}
</style>
</head>
<body>

<!-- Title slide -->
<section class="slide c1 r1">
  <div class="photo" role="img" aria-label="Galaxy swirling above a planet horizon with a lone figure on a rocky peak"
       style="left:150px;top:0;width:230px;height:214px;background:radial-gradient(ellipse at 50% 45%,#d6c3ff 0%,#7a55d8 22%,#3c2590 50%,#160a3a 85%)"></div>
  <div class="abs" style="left:-60px;top:20px;width:270px;height:270px;border-radius:50%;border:22px solid #5e33b0;background:var(--bg-deep)"></div>
  <div class="brand" style="left:50px;top:82px;font-size:11px"><i></i>LANTERN GUILD</div>
  <div class="title center" style="top:112px;width:160px;font-size:10px">WELCOME TO</div>
  <div class="title center" style="top:126px;width:160px;font-size:14.5px;font-weight:700">THE UNIVERSE</div>
  <div class="rule" style="left:52px;top:149px;width:56px"></div>
  <div class="title center" style="top:158px;width:160px;font-size:6.6px;font-weight:400">UNITING HUMANITY AS ONE</div>
</section>

<!-- Planetary NFTs -->
<section class="slide c2 r1">
  <div class="orbit" style="left:40px;top:-60px;width:300px;height:300px"></div>
  <div class="brand"><i></i>LANTERN GUILD</div>
  <div class="title center" style="top:24px">PLANETARY <b>NFT'S</b></div>
  <div class="rule" style="left:142px;top:45px;width:96px"></div>
  <div class="node" style="left:79px;top:64px;width:48px;height:48px">
    <svg viewBox="0 0 24 24" fill="none" stroke="#fff" stroke-width="1.4"><circle cx="12" cy="8" r="5"/><path d="M3 18h6l3 2 6-3"/></svg>BUY AN NFT</div>
  <div class="node" style="left:158px;top:70px;width:60px;height:60px;font-size:6.5px;letter-spacing:1px">LANTERN<br>GUILD</div>
  <div class="node" style="left:247px;top:64px;width:48px;height:48px">
    <svg viewBox="0 0 24 24" fill="none" stroke="#fff" stroke-width="1.4"><rect x="4" y="9" width="16" height="10" rx="1"/><path d="M9 9l3-5 3 5"/></svg>SELL NFT's</div>
  <div class="node" style="left:166px;top:152px;width:44px;height:44px">
    <svg viewBox="0 0 24 24" fill="none" stroke="#fff" stroke-width="1.4"><circle cx="12" cy="12" r="7"/><circle cx="12" cy="12" r="3"/></svg>EARN NFT's</div>
  <svg class="abs" style="left:142px;top:89px" width="8" height="10" viewBox="0 0 8 10"><path d="M8 0L0 5l8 5z" fill="var(--violet)"/></svg>
  <svg class="abs" style="left:226px;top:89px" width="8" height="10" viewBox="0 0 8 10"><path d="M0 0l8 5-8 5z" fill="var(--violet)"/></svg>
  <svg class="abs" style="left:183px;top:136px" width="10" height="8" viewBox="0 0 10 8"><path d="M0 0h10L5 8z" fill="var(--violet)"/></svg>
  <div class="dot" style="left:342px;top:170px;width:22px;height:22px"></div>
  <div class="dot" style="left:336px;top:186px;width:10px;height:10px;background:#5a2aa8"></div>
</section>

<!-- About -->
<section class="slide c1 r2">
  <div class="brand"><i></i>LANTERN GUILD</div>
  <div class="title" style="left:14px;top:56px;font-size:12.5px">ABOUT <b>THE UNIVERSE</b></div>
  <div class="rule" style="left:14px;top:82px;width:96px"></div>
  <div class="body" style="left:14px;top:93px;width:200px">
    <p>The Lantern Guild is a spiritual, conscious and regenerative non-profit organisation established for furthering the upliftment, enlightenment, spiritual realisation, and general welfare of people throughout the world, the betterment of life on planet Earth, and other spiritual, environmental, humanitarian, and beneficent purpose.</p>
    <p>Buddhism, Christianity, Hinduism, Islam, Judaism and other religions are belief systems; The Universe exists whether you believe in it or not.</p>
    <p>We are the Universe, and so are you.</p>
  </div>
  <div class="photo" role="img" aria-label="Rocky cliffs with a glowing cosmic portal and a small figure standing in it"
       style="left:226px;top:-10px;width:240px;height:240px;border-radius:50%;background:radial-gradient(circle at 35% 55%,#e6d8f5 0%,#9b8aa8 25%,#5b5560 55%,#2e2a30 90%)"></div>
  <div class="abs" style="left:305px;top:78px;width:86px;height:86px;border-radius:50%;background:var(--bg-deep)"></div>
</section>

<!-- Membership -->
<section class="slide c2 r2">
  <div class="brand"><i></i>LANTERN GUILD</div>
  <div class="title" style="left:14px;top:84px;font-size:12.5px;line-height:17px">MEMBERSHIP<br><b>BENEFITS</b></div>
  <div class="rule" style="left:14px;top:125px;width:58px"></div>
  <div class="abs" style="left:110px;top:27px;width:126px;height:126px;border-radius:50%;background:rgba(123,63,196,.15)"></div>
  <div class="photo" role="img" aria-label="Deep space scene with a glowing cosmic phenomenon among stars"
       style="left:123px;top:40px;width:100px;height:100px;border-radius:50%;border:4px solid #5a2aa8;background:radial-gradient(circle at 50% 50%,#4a5a9a 0%,#2c3670 45%,#151a40 100%)"></div>
  <div class="dot" style="left:222px;top:27px;width:3px;height:3px"></div>
  <div class="dot" style="left:222px;top:184px;width:3px;height:3px"></div>
  <div class="tier" style="left:234px;top:21px"><span class="ic"><svg viewBox="0 0 24 24" fill="none" stroke="#5a2aa8" stroke-width="1.6"><circle cx="12" cy="12" r="9"/><path d="M15 9l-2 4-4 2 2-4z"/></svg></span>EXPLORER: FREE</div>
  <div class="tier" style="left:267px;top:51px"><span class="ic"><svg viewBox="0 0 24 24" fill="none" stroke="#5a2aa8" stroke-width="1.6"><circle cx="9" cy="9" r="3"/><circle cx="16" cy="10" r="2.5"/><path d="M3 19c0-4 3-6 6-6s6 2 6 6M15 15c3 0 6 1 6 4"/></svg></span>MEMBER</div>
  <div class="tier" style="left:279px;top:89px"><span class="ic"><svg viewBox="0 0 24 24" fill="none" stroke="#5a2aa8" stroke-width="1.6"><path d="M6 11a6 6 0 0112 0v3H6z"/><path d="M5 20c1-4 4-5 7-5s6 1 7 5"/></svg></span>MISSIONARIES</div>
  <div class="tier" style="left:269px;top:134px"><span class="ic" style="background:var(--lilac)"><svg viewBox="0 0 24 24" fill="none" stroke="#3a1670" stroke-width="1.6"><circle cx="12" cy="9" r="4"/><path d="M5 20c1-4 4-5 7-5s6 1 7 5"/></svg></span>STEWARD</div>
  <div class="tier" style="left:236px;top:167px"><span class="ic"><svg viewBox="0 0 24 24" fill="none" stroke="#5a2aa8" stroke-width="1.6"><path d="M6 11a6 6 0 0112 0v3H6z"/><path d="M5 20c1-4 4-5 7-5s6 1 7 5"/></svg></span>MISSIONARIES</div>
</section>

<!-- Envision -->
<section class="slide c1 r3">
  <div class="orbit" style="left:60px;top:-40px;width:320px;height:320px"></div>
  <div class="abs" style="left:275px;top:105px;width:170px;height:170px;border-radius:50%;background:rgba(123,63,196,.22)"></div>
  <div class="brand"><i></i>LANTERN GUILD</div>
  <div class="title center" style="top:24px;font-size:12.5px">WHAT WE <b>ENVISION</b></div>
  <div class="rule" style="left:142px;top:45px;width:96px"></div>
  <div class="vision" style="left:30px;top:84px">
    <span class="ic"><svg viewBox="0 0 24 24" fill="none" stroke="#4a1f8a" stroke-width="1.4"><circle cx="7" cy="8" r="2"/><circle cx="12" cy="7" r="2"/><circle cx="17" cy="8" r="2"/><path d="M3 18c0-4 2-6 4-6s4 2 4 6M9 18c0-5 1-7 3-7s3 2 3 7M13 18c0-4 2-6 4-6s4 2 4 6"/></svg></span>
    <h4>PEOPLE</h4><p>A World that meets the needs of every human being as a birth right, providing the foundation for self-actualisation.</p></div>
  <div class="vision" style="left:145px;top:104px">
    <span class="ic"><svg viewBox="0 0 24 24" fill="none" stroke="#4a1f8a" stroke-width="1.4"><circle cx="12" cy="11" r="6"/><path d="M3 14c2 4 5 6 9 6s7-2 9-6"/></svg></span>
    <h4>PLANET</h4><p>A World that lives in harmony with Nature; restore and protect Mother Earth, including the Animal Kingdom.</p></div>
  <div class="vision" style="left:259px;top:84px">
    <span class="ic"><svg viewBox="0 0 24 24" fill="none" stroke="#4a1f8a" stroke-width="1.4"><path d="M4 13c4 0 7-2 9-6 1 4 4 6 7 6-3 3-7 5-11 4l-3 3"/></svg></span>
    <h4>PEACE</h4><p>A World that chooses peace, love and harmony, awake and aware of its connection with everything.</p></div>
</section>

<!-- Sponsorship -->
<section class="slide c2 r3">
  <div class="photo" role="img" aria-label="Solar system of planets above a dark mountain and desert dunes with a lone walker"
       style="left:0;top:0;width:190px;height:214px;background:linear-gradient(180deg,#0d0a22 0%,#2b2245 40%,#6d5566 62%,#a88580 80%,#6a4c55 100%)"></div>
  <div class="abs" style="left:93px;top:-40px;width:420px;height:300px;border-radius:50%;background:var(--bg)"></div>
  <div class="abs" style="left:343px;top:2px;width:60px;height:60px;border-radius:50%;background:rgba(123,63,196,.22)"></div>
  <div class="brand"><i></i>LANTERN GUILD</div>
  <div class="title" style="left:152px;top:47px;font-size:12.5px">SPONSORSHIP <b>BENEFITS</b></div>
  <div class="rule" style="left:152px;top:72px;width:58px"></div>
  <div class="body" style="left:152px;top:87px;width:224px;text-align:left">Organisations can give 5-10% of their yearly revenue as a tax-deductible sponsorship. In exchange, they will receive the same benefits as a partner organisation, excluding ministry documentation for tax-exempt banking.</div>
  <ul class="list" style="left:152px;top:124px">
    <li>Cryptocurrency</li><li>Decentralized banking</li><li>Legal support</li><li>Accounting services</li><li>Cost Reduction</li><li>Marketing support</li><li>Business support</li></ul>
  <ul class="list" style="left:227px;top:124px">
    <li>Technical support</li><li>Lantern Guild branding</li><li>Support Conscious Economy</li><li>Reach the Conscious Community</li><li>Join a community of Conscious Organisations</li><li>Access Networking events</li><li>Contribute to the Ministry Fund</li></ul>
  <div class="dot" style="left:130px;top:181px;width:9px;height:9px;background:var(--lilac)"></div>
</section>

<!-- Intentions -->
<section class="slide c1 r4">
  <div class="photo" role="img" aria-label="Colourful nebula over a dark tree silhouette at dusk"
       style="left:-2px;top:25px;width:182px;height:210px;border-radius:0 105px 105px 0;background:radial-gradient(ellipse at 40% 35%,#e27ab8 0%,#7a4bb8 28%,#2a2450 55%,#1a1428 80%)"></div>
  <div class="dot" style="left:104px;top:61px;width:22px;height:22px;background:var(--lilac)"></div>
  <div class="dot" style="left:120px;top:73px;width:11px;height:11px"></div>
  <div class="brand"><i></i>LANTERN GUILD</div>
  <div class="title" style="left:198px;top:36px;font-size:12.5px;font-weight:700">INTENTIONS</div>
  <div class="rule" style="left:198px;top:61px;width:42px"></div>
  <div class="body" style="left:198px;top:72px;width:177px">The Lantern Guild, members, missionaries, stewards, sponsors, partners, and donors are working on various initiatives to fulfil our intentions. As a collective we are focusing on every area; from education, healthcare, economics, finance, governance &amp; technology, to space travel, art, music and transformational experiences. Our mission is to protect the Spirit of Air, Water, Land and Food; to create a system that supports the people and the planet; to redistribute wealth; protect human rights; serve justice and implement the conscious economy. We are focused on building a global community, transforming local environments, integration with Indigenous tribes and the reformation of society. We are interested in new paradigm schools and Universities, incubators for regenerative technology, natural medicine, empowering micro-industries, entrepreneurs, investors, inventors, artists and creatives. If you are involved in any initiative that benefits the collective, we would love to support you.</div>
</section>

<!-- Access funding -->
<section class="slide c2 r4">
  <div class="abs" style="left:248px;top:125px;width:170px;height:170px;border-radius:50%;background:rgba(123,63,196,.35)"></div>
  <div class="brand"><i></i>LANTERN GUILD</div>
  <div class="title center" style="top:40px;font-size:12.5px">ACCESS <b>FUNDING</b></div>
  <div class="rule" style="left:147px;top:61px;width:86px"></div>
  <div class="step" style="left:38px;top:92px"><svg viewBox="0 0 24 24" fill="none" stroke="#fff" stroke-width="1.3"><circle cx="13" cy="11" r="7"/><path d="M8 16l-5 5"/></svg>BECOME AN<br>EXPLORER</div>
  <div class="step" style="left:150px;top:92px"><svg viewBox="0 0 24 24" fill="none" stroke="#fff" stroke-width="1.3"><circle cx="10" cy="8" r="4"/><path d="M3 20c1-5 4-6 7-6s4 1 5 2"/><circle cx="18" cy="17" r="3"/><path d="M18 15.5v3M16.5 17h3"/></svg>BECOME AN<br>MEMBER</div>
  <div class="step" style="left:263px;top:92px"><svg viewBox="0 0 24 24" fill="none" stroke="#fff" stroke-width="1.3"><path d="M6 11a6 6 0 0112 0v3H6z"/><path d="M4 21c1-4 4-6 8-6s7 2 8 6"/></svg>BECOME AN<br>MISSIONARY</div>
  <svg class="abs" style="left:123px;top:129px" width="24" height="6" viewBox="0 0 24 6"><path d="M0 3h20" stroke="#fff" stroke-width=".8" stroke-dasharray="2 1.5"/><path d="M20 1l3 2-3 2z" fill="#fff"/></svg>
  <svg class="abs" style="left:236px;top:129px" width="24" height="6" viewBox="0 0 24 6"><path d="M0 3h20" stroke="#fff" stroke-width=".8" stroke-dasharray="2 1.5"/><path d="M20 1l3 2-3 2z" fill="#fff"/></svg>
</section>

<!-- Partners -->
<section class="slide c1 r5">
  <div class="brand"><i></i>LANTERN GUILD</div>
  <div class="title center" style="top:24px;font-size:12.5px;font-weight:700">PARTNERS</div>
  <div class="rule" style="left:172px;top:45px;width:36px"></div>
  <div class="partner" style="left:10px;top:57px"><div class="badge" style="background:#2e2640"></div><h5>LANTERN GUILD</h5><p>A Group of Conscious Organisations</p></div>
  <div class="partner" style="left:101px;top:57px"><div class="badge" style="background:#0f0f14"></div><h5>SPROUTWELL</h5><p>Regenerative Money</p></div>
  <div class="partner" style="left:190px;top:57px"><div class="badge" style="background:#141014"></div><h5>KINDRED HANDS</h5><p>Rainbow Entrepreneurs</p></div>
  <div class="partner" style="left:280px;top:57px"><div class="badge" style="background:#1d4f7a"></div><h5>BRIGHTWAVE CIRCLE</h5><p>An ecosystem for personal growth</p></div>
  <div class="partner" style="left:10px;top:135px"><div class="badge" style="background:#ffffff"></div><h5>MYCELIO</h5><p>Regenerative Technology</p></div>
  <div class="partner" style="left:101px;top:135px"><div class="badge" style="background:#2c3a5c"></div><h5>AXIOMA</h5><p>Fast, Scalable, Decentralised<br>Finance is here with Axioma</p></div>
  <div class="partner" style="left:190px;top:135px"><div class="badge" style="background:#e8e8e8"></div><h5>COMMONPOOL</h5><p>Crowdsourced Solutions from<br>Trusted Connections.</p></div>
  <div class="partner" style="left:280px;top:135px"><div class="badge" style="background:var(--lilac)"></div><h5>LANTERN SOCIAL</h5><p>Social media for light workers<br>and communities</p></div>
</section>

<!-- Thank you -->
<section class="slide c2 r5">
  <div class="abs" style="left:328px;top:25px;width:22px;height:22px;border-radius:50%;background:rgba(123,63,196,.3)"></div>
  <div class="abs" style="left:340px;top:42px;width:11px;height:11px;border-radius:50%;background:rgba(123,63,196,.3)"></div>
  <div class="abs" style="left:14px;top:185px;width:10px;height:10px;border-radius:50%;background:rgba(123,63,196,.3)"></div>
  <div class="brand"><i></i>LANTERN GUILD</div>
  <div class="title center" style="top:24px;font-size:12.5px">THANK <b>YOU</b></div>
  <div class="rule" style="left:158px;top:45px;width:64px"></div>
  <div class="contact" style="left:43px;top:68px"><span class="ic"><svg viewBox="0 0 24 24" fill="#5a2aa8"><path d="M12 2a7 7 0 00-7 7c0 5 7 13 7 13s7-8 7-13a7 7 0 00-7-7zm0 9.5A2.5 2.5 0 1112 6.5a2.5 2.5 0 010 5z"/></svg></span><div>ADDRESS:<br>Universe address here</div></div>
  <div class="contact" style="left:147px;top:68px"><span class="ic"><svg viewBox="0 0 24 24" fill="#5a2aa8"><path d="M6.6 10.8a15 15 0 006.6 6.6l2.2-2.2a1 1 0 011-.25 11.4 11.4 0 003.6.57 1 1 0 011 1V20a1 1 0 01-1 1A17 17 0 013 4a1 1 0 011-1h3.5a1 1 0 011 1c0 1.25.2 2.45.57 3.57a1 1 0 01-.25 1z"/></svg></span><div>PHONE:<br>+1 555-010-4420</div></div>
  <div class="contact" style="left:230px;top:68px"><span class="ic"><svg viewBox="0 0 24 24" fill="#5a2aa8"><path d="M3 5h18v14H3z"/><path d="M3 5l9 7 9-7" stroke="#efe3ff" stroke-width="1.6" fill="none"/></svg></span><div>EMAIL:<br>hello@lanternguildhq.org</div></div>
  <div class="photo" role="img" aria-label="Person seated on a rock above a sea of clouds, seen from behind"
       style="left:101px;top:118px;width:180px;height:180px;border-radius:50%;background:radial-gradient(circle at 50% 40%,#9aa6b8 0%,#5d6b82 40%,#2f3a4f 75%)"></div>
</section>

</body>
</html>
```